Lanternfield Drinks business cards

We need a business card design for our new logo. The company is modern, progressive, professional, yet approachable. The key products are ready to drink bottles and cans of coffee based beverages.
These cards will be a critical part of the first impression made by our sales organization, business development team, and all external facing personnel.
Card can be a vertical or horizontal orientation.

Target Market(s)

Customers, suppliers, business partners

Industry/Entity Type

Business

Contact Information for Business Card

Business cards should feature Company Name and Logo.

Font styles to use
Serif

Colors

Designer to choose colors to be used in the design.

Requirements
Must have
• Strong readability of Name, phone #, mobile number and email address.
• Job title, website url, Street Address, and other details can be secondary level readability.
Nice to have
• High impact, simplistic quality design.
• Ok to utilize the 'H in the box' separate from the company name

```html
<!DOCTYPE html>
<html lang="en">
<head>
<meta charset="utf-8">
<title>Lanternfield Drinks business cards</title>
<link rel="stylesheet" href="https://fonts.googleapis.com/css2?family=Cinzel:wght@600;700&family=Open+Sans:wght@400;600&display=swap">
<style>
  :root {
    --backdrop: #e9e6e1;
    --card-dark: #2b2b2d;
    --card-light: #ffffff;
    --accent: #f05a28;
    --accent-gold: #f08a24;
    --ink: #2a2a2a;
    --ink-soft: #3c3c3c;
  }
  * { box-sizing: border-box; margin: 0; padding: 0; }
  html, body { width: 1200px; height: 900px; overflow: hidden; }
  body {
    background: var(--backdrop);
    position: relative;
    font-family: "Open Sans", Arial, sans-serif;
  }
  .card {
    position: absolute;
    width: 640px;
    height: 366px;
    box-shadow: 0 10px 28px rgba(0,0,0,0.18);
    overflow: hidden;
  }

  /* Front card */
  .card-front {
    left: 110px;
    top: 90px;
    background: var(--card-dark);
  }
  .front-brand {
    position: absolute;
    left: 0; right: 0;
    top: 118px;
    display: flex;
    flex-direction: column;
    align-items: center;
  }
  .brand-square {
    width: 56px;
    height: 56px;
    border: 4px solid var(--accent);
    margin-bottom: 18px;
  }
  .brand-name {
    font-family: "Cinzel", Georgia, serif;
    font-weight: 700;
    font-size: 34px;
    letter-spacing: 1px;
    color: var(--accent);
    line-height: 1;
  }
  .brand-rule {
    width: 300px;
    height: 2px;
    background: var(--accent-gold);
    margin-top: 12px;
  }

  /* Back card */
  .card-back {
    left: 450px;
    top: 440px;
    background: var(--card-light);
  }
  .side-band {
    position: absolute;
    left: 0; top: 0;
    width: 175px;
    height: 100%;
    background: var(--accent);
  }
  .side-brand {
    position: absolute;
    left: 50%;
    top: 50%;
    transform: translate(-50%, -50%) rotate(-90deg);
    display: flex;
    align-items: center;
    gap: 12px;
    white-space: nowrap;
  }
  .side-brand .brand-name { color: #fff; font-size: 27px; }
  .side-rule { width: 34px; height: 2px; background: #fff; }

  .contact {
    position: absolute;
    left: 230px;
    top: 88px;
    color: var(--ink);
  }
  .person-name {
    font-family: "Cinzel", Georgia, serif;
    font-weight: 600;
    font-size: 22px;
    color: var(--accent);
    line-height: 1.1;
  }
  .job-title {
    font-size: 14px;
    color: var(--ink-soft);
    margin-bottom: 12px;
  }
  .contact-list { list-style: none; }
  .contact-list li {
    display: flex;
    align-items: center;
    gap: 8px;
    font-size: 15px;
    line-height: 22px;
  }
  .contact-icon { width: 16px; height: 16px; flex: none; }
  .address {
    margin-top: 16px;
    font-size: 15px;
    line-height: 21px;
  }
</style>
</head>
<body>

<section class="card card-front" aria-label="Card front">
  <div class="front-brand">
    <div class="brand-square"></div>
    <div class="brand-name">Lanternfield Drinks</div>
    <div class="brand-rule"></div>
  </div>
</section>

<section class="card card-back" aria-label="Card back">
  <div class="side-band">
    <div class="side-brand">
      <div class="side-rule"></div>
      <div class="brand-name">Lanternfield Drinks</div>
      <div class="side-rule"></div>
    </div>
  </div>

  <div class="contact">
    <div class="person-name">Daniel Marsh</div>
    <div class="job-title">Managing Director</div>
    <ul class="contact-list">
      <li>
        <svg class="contact-icon" viewBox="0 0 16 16" aria-hidden="true"><rect width="16" height="16" fill="#f05a28"/><path d="M4 5.5c0-.8.6-1.2 1.2-1.2h5.6c.6 0 1.2.4 1.2 1.2v1H9.8V5.8H6.2v.7H4zM5 7.5h6l1 4H4z" fill="#fff"/></svg>
        044-987 654 321
      </li>
      <li>
        <svg class="contact-icon" viewBox="0 0 16 16" aria-hidden="true"><rect width="16" height="16" fill="#f05a28"/><rect x="5" y="3" width="6" height="10" rx="1" fill="none" stroke="#fff" stroke-width="1.4"/><circle cx="8" cy="11" r=".8" fill="#fff"/></svg>
        044-987 654 322
      </li>
      <li>
        <svg class="contact-icon" viewBox="0 0 16 16" aria-hidden="true"><rect width="16" height="16" fill="#f05a28"/><rect x="3" y="4.5" width="10" height="7" fill="none" stroke="#fff" stroke-width="1.3"/><path d="M3 4.5l5 4 5-4" fill="none" stroke="#fff" stroke-width="1.3"/></svg>
        hello@lanternfield.com
      </li>
      <li>
        <svg class="contact-icon" viewBox="0 0 16 16" aria-hidden="true"><rect width="16" height="16" fill="#f05a28"/><circle cx="8" cy="8" r="4.5" fill="none" stroke="#fff" stroke-width="1.3"/><path d="M3.5 8h9M8 3.5c-2 2.5-2 6.5 0 9M8 3.5c2 2.5 2 6.5 0 9" fill="none" stroke="#fff" stroke-width="1"/></svg>
        www.lanternfield.com
      </li>
    </ul>
    <p class="address">48 Millrace Lane, Harbour Town<br>Northshire, 204817.</p>
  </div>
</section>

</body>
</html>
```